Fernwick Landscaping Folder Design

I need a graphic designer to design a folder so we can insert informational sheets inside it for customers. The folder must include the company logo, project images, on front and back of folder and slogan " The Experience You Want, The Service You Expect, And The Value You Deserve'

Folder to also include phone numbers : 416 555 0193 as well as the website: www.fernwicklandscaping.example as well as we gurantee a 24 month warranty.

I have attached sample of size we need.

Pixel Harbor has also done something similar for me for Tollbridge Landscapes

Target Market(s)

geared toward home owners & commercial/industrial

Industry/Entity Type

Landscaping

Font styles to use
Other font styles liked:
• open to new trendy font

Requirements
Must have
• Telephone Number, email address, slogan, images,
Nice to have
• images of completed projects incorporated into the front and back of folder as well as the logo
Should not have
• n/a

```html
<!DOCTYPE html>
<html lang="en">
<head>
<meta charset="utf-8">
<title>Fernwick Landscaping Folder</title>
<link href="https://fonts.googleapis.com/css2?family=Oswald:wght@500;600&family=Roboto:wght@400;700&display=swap" rel="stylesheet">
<style>
  :root {
    --backdrop: #ecebe8;
    --paper: #ffffff;
    --charcoal: #58595b;
    --charcoal-deep: #4f5052;
    --ghost-type: #626365;
    --hex-grey: #d6d6d7;
    --hex-field: #ffffff;
    --ink: #4a4a4c;
    --spine: #c9c9c9;
  }
  * { margin: 0; padding: 0; box-sizing: border-box; }
  html, body { width: 1200px; height: 1069px; overflow: hidden; background: var(--backdrop); }
  .folder {
    position: absolute; left: 143px; top: 127px;
    width: 914px; height: 813px;
    display: flex; background: var(--paper);
    box-shadow: 0 2px 8px rgba(0,0,0,.18);
    overflow: hidden;
  }
  .panel { position: relative; width: 457px; height: 813px; }
  .panel--back { border-right: 1px solid var(--spine); }

  .hex-gallery { position: absolute; left: 0; top: 0; width: 457px; height: 488px; background: var(--hex-grey); }
  .hex-gallery svg { display: block; }

  .warranty-band {
    position: absolute; left: 0; top: 490px; width: 457px; height: 21px;
    background: var(--charcoal); color: #fff;
    font: 700 10px/21px "Roboto", sans-serif; letter-spacing: .2px;
    padding-left: 138px; text-transform: uppercase;
  }
  .contact { position: absolute; left: 137px; top: 531px; font: 400 11.5px/16px "Roboto", sans-serif; color: var(--ink); list-style: none; }
  .contact li { display: flex; align-items: center; gap: 5px; }
  .contact svg { width: 9px; height: 9px; }

  .cover-photo { position: absolute; left: 10px; top: 10px; }
  .brand-name {
    position: absolute; left: 28px; top: 462px; width: 170px; text-align: center;
    font: 600 30px/1 "Oswald", sans-serif; color: var(--charcoal); letter-spacing: 2px;
  }
  .brand-name span { display: block; font-size: 14px; letter-spacing: 3px; margin-top: 6px; }
  .slogan {
    position: absolute; left: 235px; top: 476px;
    font: 600 15.5px/16.5px "Oswald", sans-serif; color: var(--charcoal-deep);
    text-transform: uppercase;
  }

  .base-band { position: absolute; left: 0; top: 610px; width: 914px; height: 203px; background: var(--charcoal); overflow: hidden; }
  .ghost-name {
    position: absolute; left: 0; top: 0; width: 914px; height: 203px;
    display: flex; justify-content: space-between; align-items: center;
    padding: 0 12px 0 22px;
    transform: rotate(180deg);
    font: 500 205px/1 "Oswald", sans-serif; color: var(--ghost-type);
  }
</style>
</head>
<body>
<div class="folder">
  <section class="panel panel--back">
    <div class="hex-gallery">
      <svg width="457" height="488" viewBox="0 0 457 488">
        <defs>
          <path id="hex" d="M0,61 L36,0 H174 L210,61 L174,122 H36 Z"/>
          <linearGradient id="g-site" x1="0" y1="0" x2="0" y2="1"><stop offset="0" stop-color="#a8adb2"/><stop offset="1" stop-color="#c9c6bf"/></linearGradient>
          <linearGradient id="g-pool" x1="0" y1="0" x2="0" y2="1"><stop offset="0" stop-color="#5a5440"/><stop offset=".5" stop-color="#3f7fd6"/><stop offset="1" stop-color="#8c8577"/></linearGradient>
          <linearGradient id="g-mono" x1="0" y1="0" x2="0" y2="1"><stop offset="0" stop-color="#6d6d6d"/><stop offset="1" stop-color="#b9b9b9"/></linearGradient>
          <linearGradient id="g-path" x1="0" y1="0" x2="1" y2="1"><stop offset="0" stop-color="#6f7d55"/><stop offset="1" stop-color="#a9a6a0"/></linearGradient>
          <linearGradient id="g-drive" x1="0" y1="0" x2="0" y2="1"><stop offset="0" stop-color="#6f7a4c"/><stop offset=".4" stop-color="#c9c8c4"/><stop offset="1" stop-color="#bfbebb"/></linearGradient>
          <linearGradient id="g-garage" x1="0" y1="0" x2="0" y2="1"><stop offset="0" stop-color="#cfcac2"/><stop offset="1" stop-color="#a38f78"/></linearGradient>
        </defs>
        <g stroke="var(--hex-field)" stroke-width="8" stroke-linejoin="round">
          <rect x="0" y="0" width="457" height="488" fill="var(--hex-field)" stroke="none"/>
          <use href="#hex" x="-96" y="-94" fill="var(--hex-grey)"/>
          <use href="#hex" x="122" y="-94" fill="var(--hex-grey)"/>
          <use href="#hex" x="340" y="-94" fill="var(--hex-grey)"/>
          <use href="#hex" x="232" y="13" fill="var(--hex-grey)"/>
          <use href="#hex" x="-96" y="121" fill="var(--hex-grey)"/>
          <use href="#hex" x="450" y="228" fill="var(--hex-grey)"/>
          <use href="#hex" x="-96" y="335" fill="var(--hex-grey)"/>
          <use href="#hex" x="340" y="335" fill="var(--hex-grey)"/>
          <use href="#hex" x="14" y="442" fill="var(--hex-grey)"/>
          <use href="#hex" x="232" y="442" fill="var(--hex-grey)"/>
          <use href="#hex" x="14" y="13" fill="url(#g-site)" role="img" aria-label="Photo: crew pouring a commercial concrete lot"/>
          <use href="#hex" x="122" y="121" fill="url(#g-pool)" role="img" aria-label="Photo: backyard pool with stone surround at dusk"/>
          <use href="#hex" x="344" y="121" fill="url(#g-mono)" role="img" aria-label="Photo: black and white view of a finished driveway"/>
          <use href="#hex" x="14" y="228" fill="url(#g-path)" role="img" aria-label="Photo: interlocking stone walkway with garden beds"/>
          <use href="#hex" x="232" y="228" fill="url(#g-drive)" role="img" aria-label="Photo: curved concrete driveway"/>
          <use href="#hex" x="122" y="335" fill="url(#g-garage)" role="img" aria-label="Photo: interlock driveway in front of a garage"/>
        </g>
      </svg>
    </div>
    <div class="warranty-band">We gurantee a 24 month warranty</div>
    <ul class="contact">
      <li><svg viewBox="0 0 10 10"><circle cx="5" cy="5" r="5" fill="var(--ink)"/><path d="M3,2.5 L4.2,3.6 L3.8,4.4 Q4.8,6 5.6,6.2 L6.4,5.8 L7.5,7 L6.6,7.7 Q3.5,7 2.4,3.4 Z" fill="#fff"/></svg>416 555 0193</li>
      <li><svg viewBox="0 0 10 10"><circle cx="5" cy="5" r="4.4" fill="none" stroke="var(--ink)" stroke-width="1"/><ellipse cx="5" cy="5" rx="2" ry="4.4" fill="none" stroke="var(--ink)" stroke-width=".8"/><path d="M.6,5H9.4" stroke="var(--ink)" stroke-width=".8"/></svg>www.fernwicklandscaping.example</li>
    </ul>
  </section>

  <section class="panel panel--front">
    <svg class="cover-photo" width="437" height="423" viewBox="0 0 437 423" role="img" aria-label="Photo: long curved concrete driveway leading to a home among autumn trees">
      <defs>
        <linearGradient id="g-cover" x1="0" y1="0" x2="0" y2="1">
          <stop offset="0" stop-color="#3f4a2c"/>
          <stop offset=".35" stop-color="#5b6a3c"/>
          <stop offset=".55" stop-color="#b9bab6"/>
          <stop offset="1" stop-color="#9d9e9b"/>
        </linearGradient>
      </defs>
      <path d="M0,0H437V423C380,395 300,353 218,353C136,353 57,395 0,423Z" fill="url(#g-cover)"/>
    </svg>
    <div class="brand-name">FERNWICK<span>LANDSCAPING LTD.</span></div>
    <p class="slogan">The experience you want,<br>the service you expect,<br>and the value you deserve</p>
  </section>

  <div class="base-band" aria-hidden="true">
    <div class="ghost-name"><span>F</span><span>E</span><span>R</span><span>N</span><span>W</span><span>I</span><span>C</span><span>K</span></div>
  </div>
</div>
</body>
</html>
```